TA BRAMLEY BUSINESS CARD DESIGN PROJECT

We need to utilize our logo that was expertly created on PixelHarbor and now need to match this with a business card design.

```html
<!DOCTYPE html>
<html lang="en">
<head>
<meta charset="utf-8">
<title>TA BRAMLEY Business Card</title>
<link href="https://fonts.googleapis.com/css2?family=Open+Sans:wght@400;600;700&display=swap" rel="stylesheet">
<style>
  :root {
    --stage: #222223;
    --card: #1c1c1d;
    --card-edge: #151516;
    --brand-blue: #1b5bb5;
    --ink-light: #ffffff;
    --ink-soft: #d9d9d9;
    --rule: #9a9a9a;
    --pattern-dark: #121213;
    --pattern-mid: #2a2a2c;
  }
  * { margin: 0; padding: 0; box-sizing: border-box; }
  html, body {
    width: 1200px; height: 780px; overflow: hidden;
    background: var(--stage);
    font-family: "Open Sans", Arial, sans-serif;
  }
  .canvas {
    position: relative; width: 1200px; height: 780px;
    display: flex; align-items: center; justify-content: center; gap: 50px;
  }
  .card {
    position: relative; width: 540px; height: 310px;
    background: var(--card);
    box-shadow: 0 18px 40px rgba(0,0,0,.55);
    overflow: hidden;
  }

  /* front */
  .brand-name {
    position: absolute; left: 38px; top: 44px;
    display: flex; align-items: center; gap: 12px;
    color: var(--brand-blue); font-weight: 700; font-size: 34px; letter-spacing: 3px;
  }
  .brand-square { width: 26px; height: 26px; background: var(--brand-blue); }
  .divider { position: absolute; left: 0; top: 0; }
  .contact-block { position: absolute; left: 300px; top: 96px; color: var(--ink-light); }
  .person-name { color: var(--brand-blue); font-weight: 700; font-size: 25px; line-height: 1.1; }
  .person-title { font-size: 14px; margin-top: 4px; color: var(--ink-soft); }
  .contact-list { list-style: none; margin-top: 14px; font-size: 13px; }
  .contact-list li { display: flex; align-items: center; gap: 8px; margin-bottom: 6px; }
  .contact-list svg { width: 13px; height: 13px; fill: var(--brand-blue); }
  .address-band {
    position: absolute; left: 0; bottom: 22px; width: 440px; height: 28px;
    background: var(--brand-blue); color: var(--ink-light);
    font-size: 13.5px; line-height: 28px; padding-left: 26px;
  }
  .corner-block {
    position: absolute; right: 0; bottom: 0; width: 62px; height: 50px;
    background: var(--ink-light);
    clip-path: polygon(30% 0, 100% 0, 100% 100%, 0 100%);
  }

  /* back */
  .pattern-field {
    position: absolute; inset: 0;
    background: linear-gradient(120deg, var(--pattern-dark) 0%, var(--pattern-dark) 55%, var(--pattern-mid) 100%);
  }
  .back-brand {
    position: absolute; right: 150px; bottom: 70px;
    color: var(--brand-blue); font-weight: 700; font-size: 16px; letter-spacing: 2px;
  }
</style>
</head>
<body>
<main class="canvas">
  <section class="card card-front">
    <div class="brand-name"><span class="brand-square"></span>TA BRAMLEY</div>
    <svg class="divider" width="540" height="310" viewBox="0 0 540 310">
      <line x1="190" y1="230" x2="300" y2="140" stroke="var(--rule)" stroke-width="1"/>
    </svg>
    <div class="contact-block">
      <p class="person-name">Mira Valenko</p>
      <p class="person-title">Managing Director</p>
      <ul class="contact-list">
        <li><svg viewBox="0 0 24 24"><path d="M6.6 10.8a15 15 0 0 0 6.6 6.6l2.2-2.2a1 1 0 0 1 1-.25 11.4 11.4 0 0 0 3.6.6 1 1 0 0 1 1 1V20a1 1 0 0 1-1 1A17 17 0 0 1 3 4a1 1 0 0 1 1-1h3.5a1 1 0 0 1 1 1c0 1.25.2 2.45.6 3.6a1 1 0 0 1-.25 1z"/></svg>(555) 214-0637</li>
        <li><svg viewBox="0 0 24 24"><path d="M2 5h20v14H2zm2 2v.5l8 5 8-5V7z"/></svg>hello@tabramley.com</li>
        <li><svg viewBox="0 0 24 24"><circle cx="12" cy="12" r="10"/></svg>www.tabramley.com</li>
      </ul>
    </div>
    <div class="address-band">418 Harlow St. Suite 120 Denton, TX 76201</div>
    <div class="corner-block"></div>
  </section>

  <section class="card card-back">
    <div class="pattern-field" role="img" aria-label="Repeating brand pattern on black, fading to silver at the right edge"></div>
    <div class="back-brand">TA BRAMLEY</div>
  </section>
</main>
</body>
</html>
```